Business cards - BRENT Roofing & Siding

We need simple business cards made up for our Roofing & Siding business based in Calgary Alberta.
The logo on one side of the card and potentially our slogan "Built with trust, verified by time".
The other side could have:
-A small logo
-Rep name:
-Rep cell phone:
-Rep email:
-Office phone: 403-684-2093
-Website: PrairieShingleWorks.com

We would like to incorporate the colours from our logo, especially the lite blue on the jpeg file. I have attached the ai file and jpeg file. We like the colours better on the jpeg file.

I do not require a money back guarantee

```html
<!DOCTYPE html>
<html lang="en">
<head>
<meta charset="utf-8">
<title>BRENT Roofing &amp; Siding – Business Card</title>
<link rel="stylesheet" href="https://fonts.googleapis.com/css2?family=Arimo:wght@400;700&family=Montserrat:wght@500&display=swap">
<style>
  :root {
    --backdrop: #e6e6e4;
    --card-white: #ffffff;
    --brand-red: #ec1f26;
    --brand-blue: #0e69b5;
    --light-blue: #4281c3;
    --ink: #111111;
    --grey: #555555;
    --on-colour: #ffffff;
  }
  * { box-sizing: border-box; margin: 0; padding: 0; }
  html, body { width: 1200px; height: 801px; overflow: hidden; }
  body {
    background: var(--backdrop);
    font-family: "Arimo", Arial, sans-serif;
    position: relative;
  }
  .card {
    position: absolute;
    top: 246px;
    width: 540px;
    height: 308px;
    overflow: hidden;
    box-shadow: 0 6px 18px rgba(0,0,0,0.18);
  }
  .card--front { left: 40px; background: var(--card-white); }
  .card--back { left: 620px; background: var(--brand-blue); }
  .card-shapes { position: absolute; inset: 0; width: 100%; height: 100%; }

  .company-name {
    position: absolute;
    left: 34px;
    top: 70px;
    width: 280px;
    font-family: "Montserrat", sans-serif;
    font-weight: 500;
    font-size: 27px;
    letter-spacing: 3px;
    line-height: 1.25;
    color: var(--ink);
    text-transform: uppercase;
  }
  .rep {
    position: absolute;
    right: 30px;
    top: 28px;
    text-align: right;
  }
  .rep-name { font-weight: 700; font-size: 17px; color: var(--brand-red); letter-spacing: 0.3px; }
  .rep-title { font-size: 13px; color: var(--grey); margin-top: 2px; }

  .contact-list {
    position: absolute;
    left: 22px;
    top: 218px;
    list-style: none;
    color: var(--on-colour);
    font-size: 13px;
  }
  .contact-list li { display: flex; align-items: center; gap: 8px; height: 20px; }
  .contact-icon { width: 12px; height: 12px; flex: none; }

  .back-lockup {
    position: absolute;
    left: 0;
    right: 0;
    top: 108px;
    text-align: center;
    color: var(--on-colour);
    font-family: "Montserrat", sans-serif;
    font-weight: 500;
  }
  .established { font-size: 12px; letter-spacing: 2px; margin-bottom: 8px; }
  .back-name { font-size: 30px; letter-spacing: 4px; text-transform: uppercase; }
</style>
</head>
<body>

<section class="card card--front" aria-label="Card front">
  <svg class="card-shapes" viewBox="0 0 540 308" aria-hidden="true">
    <polygon class="band-red" points="0,205 350,205 290,308 0,308" fill="var(--brand-red)"/>
    <polygon class="stripe-blue" points="362,205 390,205 330,308 302,308" fill="var(--brand-blue)"/>
    <polygon class="corner-blue" points="404,205 540,205 540,308 344,308" fill="var(--light-blue)"/>
  </svg>

  <h1 class="company-name">BRENT Roofing &amp; Siding</h1>

  <div class="rep">
    <p class="rep-name">MARCUS DELANEY</p>
    <p class="rep-title">Manager</p>
  </div>

  <ul class="contact-list">
    <li>
      <svg class="contact-icon" viewBox="0 0 12 12" aria-hidden="true"><rect x="3" y="0.8" width="6" height="10.4" rx="1" fill="none" stroke="currentColor" stroke-width="1.2"/><circle cx="6" cy="9.4" r="0.6" fill="currentColor"/></svg>
      403-684-2093
    </li>
    <li>
      <svg class="contact-icon" viewBox="0 0 12 12" aria-hidden="true"><path d="M2.5 1.2 L4.6 1.2 L5.3 3.6 L4 4.6 Q5 7 7.4 8 L8.4 6.7 L10.8 7.4 L10.8 9.5 Q10.8 10.8 9.4 10.8 Q1.2 10.3 1.2 2.6 Q1.2 1.2 2.5 1.2 Z" fill="currentColor"/></svg>
      403-684-2093
    </li>
    <li>
      <svg class="contact-icon" viewBox="0 0 12 12" aria-hidden="true"><rect x="0.8" y="2.4" width="10.4" height="7.2" fill="none" stroke="currentColor" stroke-width="1.2"/><polyline points="0.8,2.4 6,6.6 11.2,2.4" fill="none" stroke="currentColor" stroke-width="1.2"/></svg>
      info@PrairieShingleWorks.com
    </li>
    <li>
      <svg class="contact-icon" viewBox="0 0 12 12" aria-hidden="true"><circle cx="6" cy="6" r="5" fill="none" stroke="currentColor" stroke-width="1.2"/><ellipse cx="6" cy="6" rx="2.2" ry="5" fill="none" stroke="currentColor" stroke-width="1"/><line x1="1" y1="6" x2="11" y2="6" stroke="currentColor" stroke-width="1"/></svg>
      PrairieShingleWorks.com
    </li>
  </ul>
</section>

<section class="card card--back" aria-label="Card back">
  <svg class="card-shapes" viewBox="0 0 540 308" aria-hidden="true">
    <polygon class="faint-band" points="0,230 540,150 540,190 0,270" fill="#ffffff" opacity="0.08"/>
    <polygon class="faint-band" points="0,285 540,205 540,235 0,308" fill="#ffffff" opacity="0.06"/>
  </svg>
  <div class="back-lockup">
    <p class="established">Est. 1991</p>
    <h2 class="back-name">BRENT Roofing &amp; Siding</h2>
  </div>
</section>

</body>
</html>
```